Business card design for holistic health care clinic

We need a double-sided business card design for our holistic health care clinic that integrates our logo design and also its color scheme. My business is called Valmira. It is an integrative medicine clinic. You have already done the logo for me. Please ensure an elegant and upscale design that is not cluttered, but still has all the necessary information (please see below for details).

Target Market(s)

Wellness, fitness, rehabilitation for educated, well-traveled open-minded clients who are focused on natural, organic, balanced and preventive healthcare and lifestyle.

Industry/Entity Type

Medical

Contact Information for Business Card

Modern, clean.

Number of Pages Required

1 page

Font styles to use
Serif
Sans Serif

Colors

Designer to choose colors to be used in the design.

Requirements
Must have
• Logo on one side, all other information on the other side.
• Other information should include:
• Tobias Wrenfeld - DOE, CPT, LMT
• 4100 East Marrow Drive
• Austin, TX 78119
• 512 555 0148
• 818 555 0192
• info@ValmiraHealth.example
• t.wrenfeld@ValmiraHealth.example
Nice to have
• Darker background on front - but not totally black - shaded/dark gray.

```html
<!DOCTYPE html>
<html lang="en">
<head>
<meta charset="utf-8">
<title>Valmira – Business Card</title>
<link rel="stylesheet" href="https://fonts.googleapis.com/css2?family=Roboto:wght@400;700&family=Roboto+Condensed:wght@700&family=Nunito:wght@700&display=swap">
<style>
  :root {
    --canvas-bg: #5b4a3b;
    --card-blue-top: #0a96d6;
    --card-blue-bottom: #0787c6;
    --card-dark-top: #252525;
    --card-dark-bottom: #2d2d2d;
    --ink: #1f1f1f;
    --brand-blue: #0a8ccc;
    --light-text: #f2f2f2;
  }
  html, body {
    margin: 0;
    padding: 0;
    width: 1200px;
    height: 960px;
    overflow: hidden;
    background: var(--canvas-bg);
  }
  .canvas {
    position: relative;
    width: 1200px;
    height: 960px;
  }
  .card {
    position: absolute;
    width: 600px;
    height: 342px;
    border-radius: 22px;
    overflow: hidden;
    box-sizing: border-box;
    box-shadow: 0 3px 6px rgba(0, 0, 0, 0.35);
  }
  .card-front {
    left: 313px;
    top: 113px;
    background: linear-gradient(180deg, var(--card-blue-top), var(--card-blue-bottom));
    color: var(--ink);
    font-family: "Roboto", Arial, sans-serif;
  }
  .card-back {
    left: 311px;
    top: 472px;
    background: linear-gradient(180deg, var(--card-dark-top), var(--card-dark-bottom));
    font-family: "Roboto", Arial, sans-serif;
  }
  .front-brand {
    position: absolute;
    right: 30px;
    top: 48px;
    margin: 0;
    font-family: "Roboto", Arial, sans-serif;
    font-weight: 700;
    font-size: 64px;
    line-height: 1;
    letter-spacing: 1px;
    color: var(--ink);
  }
  .holder {
    position: absolute;
    left: 39px;
    top: 172px;
    margin: 0;
    font-family: "Roboto Condensed", "Arial Narrow", sans-serif;
    font-weight: 700;
    font-size: 20px;
    letter-spacing: 0.2px;
    color: var(--ink);
    white-space: nowrap;
  }
  .holder .credentials {
    font-size: 12px;
    margin-left: 3px;
  }
  .contact-list {
    position: absolute;
    left: 39px;
    top: 210px;
    margin: 0;
    padding: 0;
    list-style: none;
    font-size: 14.5px;
    line-height: 19px;
  }
  .contact-list li {
    display: flex;
    align-items: center;
    height: 19px;
  }
  .contact-icon {
    width: 14px;
    height: 14px;
    margin-right: 8px;
    fill: var(--ink);
    flex: none;
  }
  .address {
    position: absolute;
    left: 39px;
    top: 294px;
    margin: 0;
    font-size: 14.5px;
    font-style: normal;
  }
  .brand-name {
    position: absolute;
    left: 0;
    right: 0;
    top: 144px;
    margin: 0;
    text-align: center;
    font-weight: 700;
    font-size: 62px;
    letter-spacing: 1px;
    line-height: 1;
    color: var(--brand-blue);
  }
  .descriptor {
    position: absolute;
    left: 0;
    right: 0;
    top: 202px;
    margin: 0;
    text-align: center;
    font-family: "Nunito", Arial, sans-serif;
    font-weight: 700;
    font-size: 19px;
    line-height: 1;
    color: var(--brand-blue);
  }
  .tagline {
    position: absolute;
    left: 0;
    right: 0;
    top: 281px;
    margin: 0;
    text-align: center;
    font-size: 14.5px;
    color: var(--light-text);
  }
</style>
</head>
<body>
<main class="canvas">
  <section class="card card-front" aria-label="Card front with contact details">
    <p class="front-brand">VALMIRA</p>
    <h1 class="holder">TOBIAS WRENFELD <span class="credentials">- DOE, CPT, LMT</span></h1>
    <ul class="contact-list">
      <li>
        <svg class="contact-icon" viewBox="0 0 16 16" aria-hidden="true"><path d="M3.6 1.2l2.3 2.6-1.4 1.9c.9 2 2.3 3.5 4.3 4.5l1.9-1.4 2.6 2.3-1 2.4c-5.6-.4-10.2-5-10.6-10.6z"/></svg>
        512 555 0148
      </li>
      <li>
        <svg class="contact-icon" viewBox="0 0 16 16" aria-hidden="true"><path d="M4 1h8v14H4zM5.5 2.5v9.5h5V2.5zM8 12.8a.9.9 0 1 0 0 1.8.9.9 0 0 0 0-1.8z" fill-rule="evenodd"/></svg>
        818 555 0192
      </li>
      <li>
        <svg class="contact-icon" viewBox="0 0 16 16" aria-hidden="true"><path d="M1.5 4h13v1l-6.5 4-6.5-4zM1.5 6.5l6.5 4 6.5-4V12h-13z"/></svg>
        t.wrenfeld@ValmiraHealth.example
      </li>
      <li>
        <svg class="contact-icon" viewBox="0 0 16 16" aria-hidden="true"><circle cx="8" cy="8" r="6.5"/><path d="M5 4.5l2 1-.5 2 2 1-1 3-2-2-.5-2zM10 3.5l1.5 2-1 1.5-1.5-1z" fill="#0a8fcf"/></svg>
        www.ValmiraHealth.example
      </li>
    </ul>
    <address class="address">4100 East Marrow Drive, Austin, TX 78119</address>
  </section>

  <section class="card card-back" aria-label="Card back with brand name">
    <p class="brand-name">VALMIRA</p>
    <p class="descriptor">Integrative Holistic Medicine</p>
    <p class="tagline">it’s all about you – your health, your objectives</p>
  </section>
</main>
</body>
</html>
```